Velvet Lantern rebranding my business with a new business card

I have my new logo and now I need a refresher on my business cards. I really want something fun and fresh. I like black background or anything to make the color pop.
Logo
Name: Velvet Lantern
Contact Info as stated below:
Mira Pellow
555-013-4762
Logo
Name: Velvet Lantern
Mira Pellow
555-013-4762
fb.me/VelvetLanternbyMira
Instagram: @VelvetLanternbyMira

Industry/Entity Type

Business

Contact Information for Business Card

double-sided. Logo on one side. Contact info on the other.

Requirements
Must have
• Logo
• Name: Velvet Lantern
• Contact Info as stated below:
• Mira Pellow
• 555-013-4762
• fb.me/VelvetLanternbyMira
• fb.me/VelvetLanternbyMira

```html
<!DOCTYPE html>
<html lang="en">
<head>
<meta charset="utf-8">
<title>Velvet Lantern – Business Card</title>
<link rel="stylesheet" href="https://fonts.googleapis.com/css2?family=Open+Sans:wght@400;600&display=swap">
<style>
  :root {
    --page-bg: #e9e6e2;
    --card-white: #ffffff;
    --card-black: #2b2b2d;
    --brand-red: #b3121a;
    --brand-pink: #d273c4;
    --name-pink: #d97ab9;
    --text-red: #b01226;
    --logo-white: #f2f2f2;
  }
  * { box-sizing: border-box; margin: 0; padding: 0; }
  html, body {
    width: 1200px; height: 900px; overflow: hidden;
    background: var(--page-bg);
    font-family: "Open Sans", Arial, sans-serif;
  }
  .canvas {
    position: relative; width: 1200px; height: 900px;
  }
  .card {
    position: absolute; left: 250px; width: 700px; height: 400px;
    box-shadow: 0 6px 18px rgba(0,0,0,.18);
    overflow: hidden;
  }
  .card--back { top: 35px; background: var(--card-black); }
  .card--front { top: 465px; background: var(--card-white); }

  .card__shapes { position: absolute; inset: 0; }

  .brand-mark {
    position: absolute; display: flex; align-items: center; gap: 12px;
    font-weight: 600; font-size: 30px; letter-spacing: .5px;
  }
  .card--back .brand-mark {
    left: 50%; top: 50%; transform: translate(-50%, -50%);
    color: var(--logo-white);
  }
  .card--front .brand-mark {
    left: 430px; top: 175px; color: var(--brand-pink);
  }
  .brand-mark__dot {
    width: 18px; height: 18px; border-radius: 50%; background: currentColor;
  }

  .holder-name {
    position: absolute; left: 70px; top: 22px;
    font-weight: 600; font-size: 22px; color: var(--name-pink);
  }

  .contact-list {
    position: absolute; left: 22px; top: 150px; list-style: none;
  }
  .contact-list__item {
    display: flex; align-items: center; gap: 10px;
    font-size: 16px; line-height: 25px; color: var(--text-red);
  }
  .contact-list__icon { width: 13px; height: 13px; flex: none; fill: var(--brand-pink); }
</style>
</head>
<body>
<main class="canvas">

  <section class="card card--back" aria-label="Card back">
    <div class="brand-mark"><span class="brand-mark__dot"></span>Velvet Lantern</div>
  </section>

  <section class="card card--front" aria-label="Card front">
    <svg class="card__shapes" width="700" height="400" viewBox="0 0 700 400" aria-hidden="true">
      <polygon points="0,0 52,0 36,24 0,24" fill="var(--brand-red)"/>
      <polygon points="40,24 62,24 50,50 18,50" fill="var(--brand-pink)"/>
      <polygon points="0,285 262,285 245,318 0,318" fill="var(--brand-red)"/>
      <polygon points="268,326 700,326 700,366 248,366" fill="var(--brand-pink)"/>
    </svg>

    <h1 class="holder-name">Mira Pellow</h1>

    <ul class="contact-list">
      <li class="contact-list__item">
        <svg class="contact-list__icon" viewBox="0 0 16 16"><path d="M3 1l3 3-2 2c1 2 3 4 5 5l2-2 3 3-2 3C6 15 1 10 1 3z"/></svg>
        555-013-4762
      </li>
      <li class="contact-list__item">
        <svg class="contact-list__icon" viewBox="0 0 16 16"><rect x="1" y="3" width="14" height="10"/><path d="M1 3l7 6 7-6" stroke="#fff" stroke-width="1.5" fill="none"/></svg>
        info@lanternmail.net
      </li>
      <li class="contact-list__item">
        <svg class="contact-list__icon" viewBox="0 0 16 16"><path d="M8 1a5 5 0 0 1 5 5c0 4-5 9-5 9S3 10 3 6a5 5 0 0 1 5-5z"/><circle cx="8" cy="6" r="2" fill="#fff"/></svg>
        www.lanternsite.net
      </li>
      <li class="contact-list__item">
        <svg class="contact-list__icon" viewBox="0 0 16 16"><circle cx="8" cy="8" r="6"/></svg>
        fb.me/VelvetLanternbyMira
      </li>
    </ul>

    <div class="brand-mark"><span class="brand-mark__dot"></span>Velvet Lantern</div>
  </section>

</main>
</body>
</html>
```